Redesign of Form/Document Navigation Page

I need a redesign of our document and navigation bar on the left. We want the same navigation bar layout/setup but want the buttons and typography to be simple and matching all over. The form needs to be aesthetically pleasing and fit within the page.

1st attachment is our Direct Deposit and the second is the form continued.

```html
<!DOCTYPE html>
<html lang="en">
<head>
<meta charset="utf-8">
<title>Employee Direct Deposit Enrollment Form</title>
<link href="https://fonts.googleapis.com/css2?family=Noto+Serif:wght@400;700&family=Arimo:wght@400;700&display=swap" rel="stylesheet">
<style>
:root{
  --navy:#213d93;
  --gold:#fbb321;
  --page:#f4f5f7;
  --panel:#ffffff;
  --line:#dfe1e5;
  --text:#6b6b6b;
  --label:#555555;
  --footer:#545454;
}
*{box-sizing:border-box;margin:0;padding:0}
html,body{width:1200px;height:901px;overflow:hidden}
body{position:relative;background:var(--page);font-family:"Noto Serif",Georgia,serif;color:var(--text)}

.site-header{position:absolute;left:0;top:0;width:1200px;height:88px;background:#fff;border-bottom:1px solid var(--line)}
.brand{position:absolute;left:25px;top:24px;display:flex;align-items:center;gap:10px}
.brand-mark{width:40px;height:40px;background:var(--navy);border-radius:4px}
.brand-name{font-family:"Noto Serif",serif;font-weight:700;font-size:18px;line-height:20px;color:var(--gold);text-transform:uppercase;white-space:nowrap}
.top-nav{position:absolute;right:27px;top:35px;display:flex;align-items:center;font-family:"Arimo",Arial,sans-serif;font-size:12px;color:#666}
.top-nav span{margin-right:22px}
.power{width:27px;height:24px;background:var(--navy);display:flex;align-items:center;justify-content:center}

.back-tab{position:absolute;left:25px;top:94px;width:119px;height:29px;background:var(--navy);color:#fff;font-family:"Arimo",Arial,sans-serif;font-weight:700;font-size:11px;display:flex;align-items:center;justify-content:center}

.side-nav{position:absolute;left:25px;top:123px;width:246px;height:568px;background:#fff;border:1px solid var(--line)}
.nav-btn{position:absolute;left:16px;width:196px;height:47px;border-radius:12px;display:flex;align-items:center;color:#fff;font-weight:700;font-size:10.5px;letter-spacing:-0.1px;text-transform:uppercase;overflow:hidden;white-space:nowrap}
.nav-btn.gold{background:var(--gold)}
.nav-btn.navy{background:var(--navy)}
.nav-btn .ico{width:60px;flex:none;height:100%;display:flex;align-items:center;justify-content:center;border-right:1px solid rgba(255,255,255,.55)}
.nav-btn .lbl{padding-left:16px;line-height:15px}
.nav-btn .lbl.tight{padding-left:6px}

.form-panel{position:absolute;left:287px;top:124px;width:886px;height:677px;background:var(--panel);border:1px solid var(--line);overflow:hidden}
.scrollbar{position:absolute;right:0;top:0;width:12px;height:100%;background:#f1f1f1;border-left:1px solid #e3e3e3}
.scrollbar .thumb{position:absolute;left:2px;top:68px;width:8px;height:288px;background:#dcdcdc;border:1px solid #c9c9c9;border-radius:2px}
.form-body{position:absolute;left:21px;top:0;width:826px}
.h-title{position:absolute;top:20px;font-size:19px;font-weight:400;color:var(--navy);white-space:nowrap}
.copy{position:absolute;font-size:10.2px;letter-spacing:-0.15px;line-height:20.2px;color:var(--text);width:826px}
.attach{position:absolute;top:139px;left:0;width:824px;height:44px;border:1px solid var(--line);border-radius:3px;display:flex;align-items:center}
.attach .hint{padding-left:17px;font-size:11px;color:#777;flex:1}
.refresh{width:145px;height:45px;background:var(--gold);color:#fff;font-family:"Arimo",Arial,sans-serif;font-weight:700;font-size:15px;display:flex;align-items:center;justify-content:center;border-radius:3px;margin-right:-1px}
.h-section{position:absolute;top:206px;font-size:19px;font-weight:400;color:var(--navy)}
.note{position:absolute;top:234px;font-family:"Arimo",Arial,sans-serif;font-size:10.5px;color:#777;white-space:nowrap}
.lead{position:absolute;top:256px;font-size:14.5px;color:#666;white-space:nowrap}
.alert{position:absolute;top:286px;font-size:11.5px;color:var(--gold);white-space:nowrap}
.choice{position:absolute;display:flex;align-items:center;font-family:"Arimo",Arial,sans-serif;font-size:11.5px;color:#555;white-space:nowrap}
.box{width:14px;height:14px;border:1px solid #cfcfcf;border-radius:3px;background:#f6f6f6;margin-right:8px}
.field-label{position:absolute;font-size:11.5px;color:var(--label);white-space:nowrap}
.field{position:absolute;width:256px;height:33px;border:1px solid #d3d3d3;border-radius:2px;background:#fff}
.amount{position:absolute;left:426px;top:516px;font-weight:700;font-size:14.5px;color:var(--gold);white-space:nowrap}
.h-important{position:absolute;top:560px;font-size:18px;color:var(--navy);font-weight:400;white-space:nowrap}
.h-important strong{font-weight:700}

.site-footer{position:absolute;left:0;top:841px;width:1200px;height:60px;background:var(--footer);color:#fff;font-family:"Arimo",Arial,sans-serif;font-size:11px}
.site-footer .copy-note{position:absolute;left:25px;top:24px}
.site-footer .code{position:absolute;right:25px;top:29px}
</style>
</head>
<body>

<header class="site-header">
  <div class="brand">
    <div class="brand-mark"></div>
    <div class="brand-name">Sentinel<br>Patrol Services</div>
  </div>
  <nav class="top-nav">
    <span>HOME</span><span>|</span><span>HELP</span>
    <div class="power">
      <svg width="12" height="12" viewBox="0 0 12 12"><path d="M3.5 3.2A4 4 0 1 0 8.5 3.2" fill="none" stroke="#fff" stroke-width="1.6" stroke-linecap="round"/><line x1="6" y1="1" x2="6" y2="6" stroke="#fff" stroke-width="1.6" stroke-linecap="round"/></svg>
    </div>
  </nav>
</header>

<div class="back-tab">BACK TO PROFILE</div>

<aside class="side-nav">
  <div class="nav-btn gold" style="top:26px"><div class="ico"><svg width="34" height="24" viewBox="0 0 34 24"><rect x="2" y="5" width="26" height="15" rx="2" fill="none" stroke="#fff" stroke-width="2"/><circle cx="15" cy="12.5" r="4" fill="none" stroke="#fff" stroke-width="2"/><rect x="22" y="14" width="10" height="7" fill="#fff"/></svg></div><div class="lbl">Direct Deposit</div></div>
  <div class="nav-btn navy" style="top:104px"><div class="ico"><svg width="34" height="30" viewBox="0 0 34 30"><circle cx="19" cy="8" r="6" fill="#fff"/><path d="M8 28c0-8 5-12 11-12s11 4 11 12z" fill="#fff"/><path d="M4 22a5 5 0 0 1 9-2M13 24a5 5 0 0 1-9 2" fill="none" stroke="#fff" stroke-width="2"/></svg></div><div class="lbl">Change W-4</div></div>
  <div class="nav-btn gold" style="top:180px"><div class="ico"><svg width="34" height="22" viewBox="0 0 34 22"><path d="M9 4L2 11l7 7M25 4l7 7-7 7M20 2l-6 18" fill="none" stroke="#fff" stroke-width="2.4" stroke-linecap="round" stroke-linejoin="round"/></svg></div><div class="lbl">Labour Code</div></div>
  <div class="nav-btn navy" style="top:257px"><div class="ico"><svg width="34" height="26" viewBox="0 0 34 26"><circle cx="10" cy="8" r="5" fill="#fff"/><path d="M1 24c0-7 4-10 9-10s9 3 9 10z" fill="#fff"/><rect x="20" y="6" width="12" height="3" fill="#fff"/><rect x="20" y="12" width="12" height="3" fill="#fff"/><rect x="20" y="18" width="12" height="3" fill="#fff"/></svg></div><div class="lbl">Personal Info</div></div>
  <div class="nav-btn gold" style="top:335px"><div class="ico"><svg width="26" height="30" viewBox="0 0 26 30"><rect x="3" y="4" width="20" height="24" rx="2" fill="none" stroke="#fff" stroke-width="2"/><rect x="9" y="1" width="8" height="5" fill="#fff"/><path d="M7 13l2 2 3-3M7 20l2 2 3-3" fill="none" stroke="#fff" stroke-width="1.6"/><rect x="14" y="13" width="6" height="2" fill="#fff"/><rect x="14" y="20" width="6" height="2" fill="#fff"/></svg></div><div class="lbl tight">Appraisel &amp; Review</div></div>
  <div class="nav-btn navy" style="top:412px"><div class="ico"><svg width="30" height="30" viewBox="0 0 30 30"><rect x="3" y="5" width="22" height="22" rx="2" fill="none" stroke="#fff" stroke-width="2.4"/><path d="M10 20l2-6L25 2l4 4-13 13z" fill="#fff"/></svg></div><div class="lbl">Write Up-Slip</div></div>
  <div class="nav-btn gold" style="top:488px"><div class="ico"><svg width="34" height="32" viewBox="0 0 34 32"><rect x="3" y="22" width="4" height="9" fill="#fff"/><rect x="10" y="18" width="4" height="13" fill="#fff"/><rect x="17" y="14" width="4" height="17" fill="#fff"/><rect x="24" y="9" width="4" height="22" fill="#fff"/><path d="M3 18L22 4M16 3h7v7" fill="none" stroke="#fff" stroke-width="2.4"/></svg></div><div class="lbl" style="padding-left:19px">Employee<br>Performance</div></div>
</aside>

<main class="form-panel">
  <div class="scrollbar"><div class="thumb"></div></div>
  <div class="form-body">
    <h1 class="h-title">Employee Direct Deposit Enrollment Form</h1>
    <p class="copy" style="top:65px">There are many variations of passages of Lorem Ipsum available, but the majority have suffered alteration in some form, by injected humour, or randomised words which don't look even slightly believable. If you are going to use a passage of Lorem Ipsum, you need to be sure there isn't anything embarrassing hidden in the middle of text. All the Lorem Ipsum generators on the Internet tend to repeat predefined chunks as necessary, making this the first true generator.</p>
    <div class="attach"><span class="hint">Attach A Voided Check Or Bank Deposit Form for the Account</span><div class="refresh">REFRESH</div></div>

    <h2 class="h-section">Account Information</h2>
    <p class="note">The last item must be for the remaining amount owed to you. To distribute to more accounts, please complete another form.</p>
    <p class="lead">Make sure to indicate what ldnd of account, along with enrolling or declining</p>
    <p class="alert">**NOTIFY PAYROLL IMMEDIATELY IF YOU CLOSE OR CHANGE BANK ACCOUNT**</p>

    <div class="choice" style="left:0;top:323px"><span class="box"></span>New Enrollment</div>
    <div class="choice" style="left:131px;top:323px"><span class="box"></span>Change Enrollment</div>
    <div class="choice" style="left:285px;top:323px"><span class="box"></span>Cancel Enrollment</div>

    <span class="field-label" style="left:0;top:367px">Bank Name:</span>
    <span class="field-label" style="left:279px;top:367px">City:</span>
    <span class="field-label" style="left:556px;top:367px">State:</span>
    <div class="field" style="left:0;top:386px"></div>
    <div class="field" style="left:279px;top:386px"></div>
    <div class="field" style="left:556px;top:386px"></div>

    <span class="field-label" style="left:0;top:439px">Routing Transit #:</span>
    <span class="field-label" style="left:279px;top:439px">Account Number:</span>
    <div class="field" style="left:0;top:458px"></div>
    <div class="field" style="left:279px;top:458px"></div>

    <div class="choice" style="left:0;top:515px"><span class="box"></span>Checking</div>
    <div class="choice" style="left:129px;top:515px"><span class="box"></span>Savings</div>
    <div class="amount">Amount: 100%</div>

    <h2 class="h-important"><strong>IMPORTANT!</strong> Please read and sign before completing and submitting</h2>
    <p class="copy" style="top:608px">There are many variations of passages of Lorem Ipsum available, but the majority have suffered alteration in some form, by injected humour, or randomised words which don't look even slightly believable. If you are going to use a passage of Lorem Ipsum, you need to be sure there isn't anything embarrassing hidden in the middle of text. All the Lorem Ipsum generators on the Internet tend to repeat predefined chunks as necessary, making this the first true generator.</p>
  </div>
</main>

<footer class="site-footer">
  <span class="copy-note">Copyright © 2016&nbsp; SPS.All Rights Reserved.</span>
  <span class="code">C19</span>
</footer>

</body>
</html>
```